Thornvale Group needs a business card design

We need a new business card design using the logo recently selected in a logo competition on Pixel Bazaar. Our business is a consultancy specializing in aviation and energy and the winning business card design will promote an image of precision and professionalism with creativity.

Please use the logo with the name on the front of the card and use a complementary font. Make the back white with either the light grey or dark grey logo.

Target Market(s)

Senior finance and legal leaders at aviation and energy companies

Industry/Entity Type

Management Consulting

Contact Information for Business Card

Peter Castrell
President
Thornvale Group

www.thornvalegroup.example

(555) 204-6391
pc@thornvalegroup.example

Requirements
Must have
• Professional font that goes well with the logo font

```html
<!DOCTYPE html>
<html lang="en">
<head>
<meta charset="utf-8">
<title>Thornvale Group – Business Card</title>
<link rel="stylesheet" href="https://fonts.googleapis.com/css2?family=Open+Sans:wght@300;400;700&display=swap">
<style>
  :root {
    --backdrop: #e8e5e1;
    --navy-deep: #123c66;
    --navy-mid: #1d5a8a;
    --navy-light: #3a86b4;
    --ink-blue: #1f4e7a;
    --paper: #ffffff;
    --soft-white: #dfe8f1;
    --grey-text: #7b8590;
  }
  * { box-sizing: border-box; margin: 0; padding: 0; }
  html, body {
    width: 1200px; height: 913px; overflow: hidden;
    background: var(--backdrop);
    font-family: "Open Sans", Arial, sans-serif;
  }
  .canvas { position: relative; width: 1200px; height: 913px; }

  .card {
    position: absolute;
    width: 540px; height: 309px;
    border-radius: 4px;
    overflow: hidden;
    box-shadow: 0 10px 28px rgba(0,0,0,.18);
  }

  /* Front */
  .card-front {
    left: 60px; top: 110px;
    background: linear-gradient(160deg, var(--navy-light) 0%, var(--navy-mid) 45%, var(--navy-deep) 100%);
  }
  .front-brand {
    position: absolute; right: 34px; top: 48px;
    display: flex; align-items: center; gap: 10px;
    color: var(--paper);
    font-weight: 300; font-size: 26px; letter-spacing: 2px;
  }
  .brand-dot { width: 12px; height: 12px; border-radius: 50%; background: var(--paper); }
  .divider {
    position: absolute; left: 205px; right: 0; top: 168px;
    height: 1px; background: rgba(255,255,255,.75);
  }
  .holder { position: absolute; left: 30px; top: 140px; color: var(--paper); }
  .holder-name { font-weight: 700; font-size: 20px; line-height: 1.1; }
  .holder-role { font-weight: 300; font-size: 13px; color: var(--soft-white); margin-top: 4px; }

  .contact-panel {
    position: absolute; left: 300px; right: 0; top: 190px; bottom: 0;
    background: var(--paper);
    padding: 18px 22px 0 0;
  }
  .contact-list { list-style: none; text-align: right; color: var(--ink-blue); font-size: 13px; line-height: 22px; }
  .contact-list li { display: flex; justify-content: flex-end; align-items: center; gap: 7px; }
  .contact-list svg { width: 11px; height: 11px; fill: none; stroke: var(--grey-text); stroke-width: 1.6; }

  /* Back */
  .card-back {
    left: 600px; top: 440px;
    background: var(--paper);
    display: flex; align-items: center; justify-content: center;
  }
  .back-brand {
    display: flex; align-items: center; gap: 14px;
    color: var(--ink-blue);
    font-weight: 300; font-size: 38px; letter-spacing: 3px;
  }
  .back-brand .brand-dot { width: 16px; height: 16px; background: var(--ink-blue); }
</style>
</head>
<body>
<main class="canvas">
  <section class="card card-front" aria-label="Card front">
    <div class="front-brand"><span class="brand-dot"></span><span>Thornvale Group</span></div>
    <div class="divider"></div>
    <div class="holder">
      <p class="holder-name">Peter Castrell</p>
      <p class="holder-role">President</p>
    </div>
    <div class="contact-panel">
      <ul class="contact-list">
        <li>(555) 204-6391
          <svg viewBox="0 0 12 12"><path d="M3 1 L5 3.5 L4 5 Q5.5 7 7 8 L8.5 7 L11 9 L9.5 11 Q4 10 1 2.5 Z"/></svg></li>
        <li>pc@thornvalegroup.example
          <svg viewBox="0 0 12 12"><rect x="1" y="2.5" width="10" height="7"/><path d="M1 2.5 L6 6.5 L11 2.5"/></svg></li>
        <li>www.thornvalegroup.example
          <svg viewBox="0 0 12 12"><circle cx="6" cy="6" r="5"/><path d="M1 6 H11 M6 1 Q3 6 6 11 Q9 6 6 1"/></svg></li>
      </ul>
    </div>
  </section>

  <section class="card card-back" aria-label="Card back">
    <div class="back-brand"><span class="brand-dot"></span><span>Thornvale Group</span></div>
  </section>
</main>
</body>
</html>
```